A Spin Above Par Company Brochure

I am the owner of a Mobile Disc Jockey company specializing in weddings. I am looking for a Tri Fold color brochure that is modern and eye catching with the focus being on upscale wedding events. I also want it to be easy to read and not overly cluttered ! I would like it to reflect our website located at aspinabovepar.example
I also have different variations and file types of my logo such as jpeg and png files. I need some good dance floor pics. If you do not have any good stock photos I can look through my photo library. I uploaded a logo and pic I found from one of my videos. Not sure if it is worth anything.
We also do Uplighting and Photo Booths which I would like in the brochure. Much of the text copy needed can be taken from our website if needed. Please refer to the website to see what we do and our style.

Target Market(s)

upscale weddings

Industry/Entity Type

wedding dj entertainment & masters of ceremonies

Requirements
Nice to have
• nice pictures of packed dance floors and people having fun

```html
<!DOCTYPE html>
<html lang="en">
<head>
<meta charset="utf-8">
<title>A Spin Above Par – Brochure Inside Spread</title>
<link rel="stylesheet" href="https://fonts.googleapis.com/css2?family=Montserrat:wght@500&family=Quicksand:wght@500;600&display=swap">
<style>
  :root{
    --violet:#6600ff;
    --pink:#ff0a6c;
    --ink:#1d1530;
    --white:#ffffff;
    --warm:#c7a58f;
    --haze-1:#c4a3f0;
    --haze-2:#a286dc;
    --haze-3:#6f6a9e;
    --glow:#f4e4ff;
    --orchid:#d8a8f6;
  }
  *{box-sizing:border-box;margin:0;padding:0}
  html,body{width:1200px;height:849px;overflow:hidden;background:var(--white)}
  .spread{position:relative;width:1200px;height:849px;overflow:hidden}

  .dance-photo{
    position:absolute;inset:0;
    background:
      radial-gradient(ellipse 150px 230px at 520px 470px, rgba(255,255,255,.85) 0%, rgba(255,255,255,0) 70%),
      radial-gradient(ellipse 140px 200px at 640px 560px, rgba(248,236,255,.8) 0%, rgba(248,236,255,0) 70%),
      radial-gradient(ellipse 260px 160px at 560px 180px, var(--glow) 0%, rgba(244,228,255,0) 70%),
      radial-gradient(ellipse 200px 300px at 880px 330px, var(--orchid) 0%, rgba(216,168,246,0) 70%),
      radial-gradient(ellipse 220px 180px at 90px 90px, var(--warm) 0%, rgba(199,165,143,0) 75%),
      radial-gradient(ellipse 360px 300px at 120px 640px, var(--haze-3) 0%, rgba(111,106,158,0) 75%),
      radial-gradient(ellipse 360px 260px at 1090px 700px, var(--haze-3) 0%, rgba(111,106,158,0) 75%),
      radial-gradient(ellipse 220px 200px at 1150px 60px, #b79be6 0%, rgba(183,155,230,0) 75%),
      linear-gradient(165deg, var(--haze-1) 0%, #b392ea 40%, var(--haze-2) 72%, #857ab7 100%);
  }

  .tab{position:absolute;width:275px;height:72px;background:var(--violet)}
  .tab--top{top:0;border-radius:0 0 22px 22px}
  .tab--bottom{bottom:0;height:67px;border-radius:22px 22px 0 0}
  .tab--pink{background:var(--pink)}
  .tab--left{left:76px}
  .tab--mid{left:447px}
  .tab--right{left:835px}

  .pill{
    position:absolute;width:275px;height:43px;border-radius:22px;
    background:var(--violet);color:var(--white);
    font-family:"Montserrat",sans-serif;font-weight:500;font-size:21px;
    letter-spacing:.4px;display:flex;align-items:center;justify-content:center;
  }
  .pill--pink{background:var(--pink)}

  .copy{
    position:absolute;width:323px;
    font-family:"Quicksand",sans-serif;font-weight:500;font-size:16.3px;
    line-height:19.6px;color:var(--ink);text-align:justify;
    hyphens:auto;-webkit-hyphens:auto;
  }
  .copy p + p{margin-top:19.6px}

  .brandmark{
    position:absolute;width:315px;height:100px;
    display:flex;align-items:center;gap:12px;
    font-family:"Quicksand",sans-serif;font-weight:600;font-size:30px;
    color:var(--violet);white-space:nowrap;
  }
  .brandmark__dot{width:18px;height:18px;border-radius:50%;background:var(--violet);flex:none}

  .web{
    position:absolute;left:447px;bottom:0;width:275px;height:67px;
    display:flex;align-items:center;justify-content:center;
    color:var(--white);font-family:"Montserrat",sans-serif;font-weight:500;font-size:18px;
  }
</style>
</head>
<body>
<main class="spread">
  <div class="dance-photo" role="img" aria-label="Violet-tinted photo of a bride and groom dancing on a packed, lit dance floor"></div>

  <div class="tab tab--top tab--left"></div>
  <div class="tab tab--top tab--mid tab--pink"></div>
  <div class="tab tab--top tab--right"></div>

  <h2 class="pill" style="left:76px;top:95px">WEDDINGS</h2>
  <h2 class="pill" style="left:456px;top:94px">UPLIGHTING</h2>
  <h2 class="pill" style="left:835px;top:94px">PHOTO BOOTH</h2>
  <h2 class="pill pill--pink" style="left:76px;top:360px">CORPORATE EVENTS</h2>

  <div class="copy" style="left:52px;top:158px">
    <p>Beginning with your initial consultation, we listen to you and respond with creative ideas and helpful advice so your event is all about you. We know it’s more than just great music, it’s keeping you guests engaged and coordinating with your venue and vendors for a smooth and timely event everyone will never forget.</p>
  </div>

  <div class="copy" style="left:52px;top:432px">
    <p>With over 30+ years of experience providing DJ entertainment and lighting services for corporate events and company parties, we understand how important creating the right atmosphere and delivering quality entertainment is to the success of your event. So whether you’re planning a sales incentive meeting, awards presentation, beach party, holiday party or gala evening, let us help you create an event your employees will never forget.</p>
  </div>

  <div class="copy" style="left:432px;top:158px">
    <p>Simply put, Uplighting turns ordinary rooms into extraordinary rooms. It adds color and warmth to any room and creates a totally different atmosphere. In addition it adds to your photo’s.</p>
    <p>Uplighting fixtures are placed on the floor pointing up projecting color on surfaces such as columns, alcoves, corners and any other piece of architecture that you want to stand out.</p>
    <p>Walls can be washed with a specific color or colors to transform a rooms existing color or add additional colors. Centerpiece and linen colors can be matched to enhance and pull together the ambiance of the room. Cake table uplighting is a great example of how the use of colored uplights in a static color or in a strobing pattern can bring focus and attention to that wedding cake you spent hundreds of dollars for.</p>
    <p>Today’s LED technology offers a lot more advantages over the traditional incandescent lighting fixtures. LED fixtures are smaller and more discreet, do not get hot, draw little to no power and have the capability of producing virtually any color or tint you want.</p>
  </div>

  <div class="copy" style="left:811px;top:158px">
    <p>It’s no secret photo booths have been a hit at weddings as well as any other event. Our photo booth offers a modern sleek look and is so simple to operate it doesn’t need an attendant. However we want you and your guests to have the best experience possible so we provide one as part of our package.</p>
    <p>The combination of the right props and a fun and friendly attendant will even arouse the curiosity of your shyest guests. Once they leave the photo booth they head to the dance floor to continue the fun.</p>
    <p>It’s as easy as grabbing a prop and touching the screen. Instantly we text it to your phone or email it to you. From their you can share it to any social media site you want or share it with family and friends.</p>
  </div>

  <div class="brandmark" style="left:57px;top:664px"><span class="brandmark__dot"></span>A Spin Above Par</div>
  <div class="brandmark" style="left:816px;top:664px"><span class="brandmark__dot"></span>A Spin Above Par</div>

  <div class="tab tab--bottom tab--left"></div>
  <div class="tab tab--bottom tab--mid tab--pink"></div>
  <div class="tab tab--bottom tab--right"></div>
  <div class="web">ASPINABOVEPAR.EXAMPLE</div>
</main>
</body>
</html>
```